Life Coaching and Personal Development Business. Needs Business Card with Logo

We are a Life Coaching and Personal Development Business based in Melbourne, Victoria. We specialise in assisting Individuals who find themselves at cross roads due to career, relationships or just life experiences that are preventing them from having extraordinary lives in happiness, finance or relationships or just being disconnected from a sense of purpose. Our motto is "we help you get there".

Reason: I am awaiting final concepts from a couple of designers

Reason: Deadline passed so now would like to see more options.

Target Market(s)

Individuals who want to move through the cross roads and who are aware that they require help to do so. They are seeking happy, for filing lives through all aspects career, relationships, family and finance

Industry/Entity Type

Finance

Font styles to use
Script

Requirements
Must have
• logo which is representative of moving forward
Business Name: RD Maple Harbour
ABN: 5038617294

I do not have a preference with colour but I do not want red orange or green

Should not have
• The card must not be to busy.

```html
<!DOCTYPE html>
<html lang="en">
<head>
<meta charset="utf-8">
<title>RD Maple Harbour – Business Card</title>
<link rel="stylesheet" href="https://fonts.googleapis.com/css2?family=Tinos:ital,wght@0,400;1,400&display=swap">
<style>
  :root {
    --page: #ffffff;
    --card-front: #ffffff;
    --frame: #7a86a8;
    --brand-blue: #0b4f93;
    --back-blue: #074a86;
    --back-faint: #2a6aa5;
    --ink: #1c1c1c;
    --divider: #9a9a9a;
    --on-blue: #ffffff;
  }
  * { box-sizing: border-box; margin: 0; padding: 0; }
  html, body {
    width: 924px; height: 1200px; overflow: hidden;
    background: var(--page);
    font-family: "Tinos", "Times New Roman", serif;
  }
  .canvas { position: relative; width: 924px; height: 1200px; }

  .card-front {
    position: absolute; left: 46px; top: 42px; width: 832px; height: 535px;
    background: var(--card-front); border: 1px solid var(--frame);
  }
  .brand-name {
    position: absolute; left: 139px; top: 245px; width: 195px;
    text-align: right; color: var(--brand-blue);
    font-size: 27px; line-height: 1.15; white-space: nowrap;
  }
  .divider {
    position: absolute; left: 358px; top: 200px; width: 1px; height: 135px;
    background: var(--divider);
  }
  .contact-front { position: absolute; left: 386px; top: 234px; color: var(--ink); }
  .person-name { font-size: 23px; letter-spacing: 0.3px; line-height: 28px; }
  .phone { display: flex; align-items: center; gap: 6px; margin-top: 8px; font-size: 23px; line-height: 28px; }
  .phone svg { width: 14px; height: 22px; }

  .card-back {
    position: absolute; left: 46px; top: 656px; width: 829px; height: 534px;
    background: var(--back-blue); overflow: hidden;
  }
  .back-mark {
    position: absolute; left: 0; right: 0; top: 100px; text-align: center;
    color: var(--back-faint); font-size: 56px; line-height: 1.1; white-space: nowrap;
  }
  .motto {
    position: absolute; left: 0; right: 0; top: 222px; text-align: center;
    color: var(--on-blue); font-style: italic; font-size: 63px; line-height: 1.2; white-space: nowrap;
  }
  .contact-back {
    position: absolute; left: 0; right: 0; top: 456px; text-align: center;
    color: var(--on-blue); font-size: 20px; line-height: 30px;
  }
  .contact-back .line { display: flex; justify-content: center; align-items: center; gap: 6px; }
  .contact-back svg { width: 18px; height: 16px; }
</style>
</head>
<body>
<main class="canvas">
  <section class="card-front">
    <div class="brand-name">RD Maple<br>Harbour</div>
    <div class="divider"></div>
    <div class="contact-front">
      <p class="person-name">CLARA WHITMORE</p>
      <p class="phone">
        <svg viewBox="0 0 14 22" aria-hidden="true">
          <rect x="1" y="1" width="12" height="20" rx="2" fill="none" stroke="#0b4f93" stroke-width="2"/>
          <rect x="3" y="4" width="8" height="12" fill="#0b4f93" opacity="0.25"/>
          <circle cx="7" cy="18.3" r="1" fill="#0b4f93"/>
        </svg>
        04150 00312
      </p>
    </div>
  </section>

  <section class="card-back">
    <div class="back-mark">RD Maple Harbour</div>
    <p class="motto">"We help you get there"</p>
    <div class="contact-back">
      <p class="line">
        <svg viewBox="0 0 18 12" aria-hidden="true">
          <rect x="0.5" y="0.5" width="17" height="11" fill="none" stroke="#fff"/>
          <path d="M0.5 0.5 L9 7 L17.5 0.5 M0.5 11.5 L7 5.5 M17.5 11.5 L11 5.5" fill="none" stroke="#fff"/>
        </svg>
        clara@mapleharbour.com.au
      </p>
      <p class="line">
        <svg viewBox="0 0 12 16" aria-hidden="true">
          <path d="M6 0 C2.7 0 0 2.6 0 5.8 C0 10 6 16 6 16 C6 16 12 10 12 5.8 C12 2.6 9.3 0 6 0 Z" fill="#fff"/>
          <circle cx="6" cy="5.8" r="2.2" fill="#074a86"/>
        </svg>
        P.O. Box 4210, Seaview VIC 3100
      </p>
    </div>
  </section>
</main>
</body>
</html>
```